I need a business card design for a new business based in South West Australia.
I specialize in residential window cleaning & general handyman maintenance.

Dale Marsh - 412 SILVER HAWK DETAILING
- Window Cleaning
- House Maintenance

```html
<!DOCTYPE html>
<html lang="en">
<head>
<meta charset="utf-8">
<title>412 Silver Hawk Detailing – Business Card</title>
<link rel="stylesheet" href="https://fonts.googleapis.com/css2?family=Tinos:wght@400;700&display=swap">
<style>
  :root {
    --page-bg: #e9e6e1;
    --card-light: #eeeeee;
    --photo-tone-a: #f4f4f3;
    --photo-tone-b: #c9c7c3;
    --photo-tone-c: #dcdad6;
    --band-black: #050505;
    --band-red: #8e1216;
    --ink-dark: #0d0d0d;
    --ink-light: #ffffff;
  }
  * { margin: 0; padding: 0; box-sizing: border-box; }
  html, body {
    width: 1200px;
    height: 892px;
    overflow: hidden;
    background: var(--page-bg);
  }
  .card {
    position: absolute;
    left: 110px;
    top: 166px;
    width: 980px;
    height: 560px;
    background: var(--card-light);
    box-shadow: 0 6px 24px rgba(0,0,0,0.18);
    overflow: hidden;
    font-family: "Tinos", "Times New Roman", serif;
  }
  .card-art {
    position: absolute;
    inset: 0;
    width: 100%;
    height: 100%;
  }
  .company-name {
    position: absolute;
    left: 40px;
    top: 70px;
    font-size: 42px;
    font-weight: 700;
    letter-spacing: 1px;
    color: var(--ink-dark);
    white-space: nowrap;
  }
  .tagline {
    position: absolute;
    left: 120px;
    top: 138px;
    font-size: 28px;
    font-weight: 700;
    line-height: 38px;
    color: var(--ink-dark);
    white-space: nowrap;
  }
  .owner-name {
    position: absolute;
    left: 240px;
    top: 225px;
    font-size: 58px;
    font-weight: 700;
    color: var(--ink-dark);
    white-space: nowrap;
  }
  .services {
    position: absolute;
    left: 640px;
    top: 355px;
    list-style: none;
    font-size: 32px;
    font-weight: 700;
    line-height: 58px;
    color: var(--ink-light);
    white-space: nowrap;
  }
  .services li:nth-child(2) { padding-left: 40px; }
</style>
</head>
<body>
  <section class="card" aria-label="Business card front">
    <svg class="card-art" viewBox="0 0 980 560">
      <defs>
        <linearGradient id="photoTone" x1="0" y1="0" x2="1" y2="1">
          <stop offset="0" stop-color="#f4f4f3"/>
          <stop offset="0.5" stop-color="#dcdad6"/>
          <stop offset="1" stop-color="#c9c7c3"/>
        </linearGradient>
      </defs>
      <rect class="photo-area" role="img" aria-label="Faded photo of a worker cleaning tall windows with a brush" x="0" y="0" width="980" height="560" fill="url(#photoTone)"/>
      <path class="band-red" d="M270,560 C440,540 535,420 615,300 C695,180 755,60 835,0 L980,0 L980,560 Z" fill="#8e1216"/>
      <path class="band-black" d="M300,560 C470,540 562,420 642,300 C722,180 782,60 862,0 L980,0 L980,560 Z" fill="#050505"/>
    </svg>
    <h1 class="company-name">412 SILVER HAWK DETAILING</h1>
    <p class="tagline">residential window cleaning &amp;<br>general handyman maintenance</p>
    <p class="owner-name">Dale Marsh</p>
    <ul class="services">
      <li>Window Cleaning</li>
      <li>House Maintenance</li>
    </ul>
  </section>
</body>
</html>
```